Current state of Man's Soul Christian view

I would like an improvement of my design or a reimagining of my design to help people visualize what happens to the soul after we die. The second picture "screenshot 2023" is not my design but gives another idea.

For further information, there are 4 "time" frames that could be sectioned off. Eden is one time. Then adam rebellion and pre messiah earth (with hades/ Sheol). The third time frame is Jesus death, resurrection with the current state of earth. The 4th time frame is the "heavenly realm" which is across all 3 times and is unchanged.

For color ideas, please see my website www.lanternfieldnotes.org which has my color theme. But the death of Jesus I would like in some type of red as well as the death of believers.

My goal is something simple, engaging, and easy to understand. If you have any questions please lmk.
Thank you for considering my project.

```html
<!DOCTYPE html>
<html lang="en">
<head>
<meta charset="utf-8">
<title>Current State of Man's Soul</title>
<link rel="stylesheet" href="https://fonts.googleapis.com/css2?family=Montserrat:wght@600;700;800&display=swap">
<style>
  :root {
    --bg-top: #52e3ad;
    --bg-mid: #5aeeb0;
    --bg-bottom: #4fdd9f;
    --arrow-green: #1ff01f;
    --death-lime: #c8f23c;
    --jesus-red: #e2185c;
    --white: #ffffff;
    --label-dark: #111111;
    --fire-a: #ff5a2a;
    --fire-b: #5a0d08;
    --earth-a: #3e7fc8;
    --earth-b: #0a1a34;
    --eden-a: #4e5a56;
    --eden-b: #2c3432;
    --paradise-a: #9cc4d8;
    --paradise-b: #3e6c86;
    --torment-a: #6a3a1c;
    --torment-b: #140c08;
  }
  html, body { margin: 0; padding: 0; overflow: hidden; }
  body { width: 1200px; height: 480px; }
  .diagram {
    display: block; width: 1200px; height: 480px;
    font-family: "Montserrat", sans-serif;
  }
  .stage-label, .title, .bar-text, .arrow-text, .realm-text {
    fill: var(--white);
    filter: drop-shadow(1px 1px 1px rgba(0,0,0,0.45));
  }
  .title { font-size: 24px; font-weight: 800; }
  .stage-label { font-size: 11.5px; font-weight: 700; }
  .realm-text { font-size: 11px; font-weight: 700; }
  .bar-text { font-size: 16px; font-weight: 800; letter-spacing: 2px; }
  .arrow-text { font-size: 16px; font-weight: 800; letter-spacing: 2.5px; }
  .gate-text { font-size: 8px; font-weight: 700; fill: var(--label-dark); }
  .outline { stroke: var(--white); stroke-width: 2.5; }
  .green-arrow { fill: var(--arrow-green); }
  .death-bar { fill: var(--death-lime); }
  .jesus-red { fill: var(--jesus-red); }
  .gate-arrow { fill: var(--white); }
</style>
</head>
<body>
<svg class="diagram" viewBox="0 0 1200 480" xmlns="http://www.w3.org/2000/svg">
  <defs>
    <linearGradient id="sky" x1="0" y1="0" x2="0" y2="1">
      <stop offset="0" stop-color="var(--bg-top)"/>
      <stop offset="0.5" stop-color="var(--bg-mid)"/>
      <stop offset="1" stop-color="var(--bg-bottom)"/>
    </linearGradient>
    <radialGradient id="fire" cx="0.45" cy="0.5" r="0.6">
      <stop offset="0" stop-color="#ffd37a"/>
      <stop offset="0.45" stop-color="var(--fire-a)"/>
      <stop offset="1" stop-color="var(--fire-b)"/>
    </radialGradient>
    <radialGradient id="earth" cx="0.4" cy="0.4" r="0.7">
      <stop offset="0" stop-color="#8fb8d8"/>
      <stop offset="0.5" stop-color="var(--earth-a)"/>
      <stop offset="1" stop-color="var(--earth-b)"/>
    </radialGradient>
    <radialGradient id="eden" cx="0.5" cy="0.5" r="0.6">
      <stop offset="0" stop-color="var(--eden-a)"/>
      <stop offset="1" stop-color="var(--eden-b)"/>
    </radialGradient>
    <linearGradient id="paradise" x1="0" y1="0" x2="0" y2="1">
      <stop offset="0" stop-color="var(--paradise-b)"/>
      <stop offset="1" stop-color="var(--paradise-a)"/>
    </linearGradient>
    <linearGradient id="torment" x1="0" y1="0" x2="0" y2="1">
      <stop offset="0" stop-color="var(--torment-b)"/>
      <stop offset="1" stop-color="var(--torment-a)"/>
    </linearGradient>
  </defs>

  <rect class="background" width="1200" height="480" fill="url(#sky)"/>

  <text class="title" x="601" y="58" text-anchor="middle">3rd Heaven - God’s Heavenly Throne</text>

  <!-- Eden -->
  <g class="eden-stage">
    <circle class="outline" cx="124" cy="302" r="62" fill="url(#eden)" role="img" aria-label="Garden of Eden scene with trees and a figure"/>
    <text class="stage-label" x="124" y="309" text-anchor="middle" style="font-size:17px">Eden</text>
  </g>

  <!-- Adam rebellion -->
  <g class="rebellion-stage">
    <text class="stage-label" x="219" y="141" text-anchor="middle">Adam</text>
    <text class="stage-label" x="219" y="155" text-anchor="middle">Rebellion</text>
    <rect class="death-bar outline" x="204" y="171" width="30" height="255" rx="15"/>
    <text class="bar-text" transform="translate(225 298) rotate(-90)" text-anchor="middle">Death</text>
  </g>

  <!-- Pre-messiah -->
  <g class="pre-messiah-stage">
    <text class="stage-label" x="369" y="141" text-anchor="middle">Pre-messiah</text>
    <text class="stage-label" x="369" y="155" text-anchor="middle">Fallen Earth</text>
    <circle class="outline" cx="370" cy="236" r="61" fill="url(#fire)" role="img" aria-label="Earth engulfed in fiery red swirling clouds"/>
    <g class="hades">
      <path class="outline" d="M309,366 A61,61 0 0 1 431,366 Z" fill="url(#paradise)" role="img" aria-label="Paradise with clouds and light"/>
      <path class="outline" d="M309,366 A61,61 0 0 0 431,366 Z" fill="url(#torment)" role="img" aria-label="Dark fiery place of torment"/>
      <text class="realm-text" x="369" y="346" text-anchor="middle">Paradise</text>
      <text class="realm-text" x="369" y="400" text-anchor="middle">Torment</text>
    </g>
    <text class="stage-label" x="369" y="452" text-anchor="middle">Hades / Sheol</text>
    <path class="gate-arrow" d="M243,332 H302 V326 L320,345 L302,364 V358 H243 Z"/>
    <text class="gate-text" x="274" y="348" text-anchor="middle">Narrow Gate</text>
    <path class="gate-arrow" d="M243,381 H302 V375 L320,394 L302,413 V407 H243 Z"/>
    <text class="gate-text" x="275" y="397" text-anchor="middle">Wide Gate</text>
  </g>

  <!-- Jesus death -->
  <g class="jesus-death">
    <path class="jesus-red outline" d="M471,339 H452 V330 L436,347 L452,364 V355 H471 Z"/>
    <rect class="jesus-red outline" x="475" y="180" width="32" height="246" rx="16"/>
    <text class="bar-text" transform="translate(498 302) rotate(-90)" text-anchor="middle">Jesus Death</text>
  </g>

  <!-- Resurrection -->
  <g class="resurrection">
    <path class="green-arrow outline" d="M530,438 V119 H517 L553,79 L589,119 H577 V438 Z"/>
    <text class="arrow-text" transform="translate(559 282) rotate(-90)" text-anchor="middle">Jesus Resurrection</text>
  </g>

  <!-- Holy Spirit -->
  <g class="holy-spirit">
    <path class="green-arrow outline" d="M603,89 H650 V207 H776 V193 L818,230 L776,267 V254 H603 Z"/>
    <text class="arrow-text" transform="translate(620 108) rotate(90)" style="font-size:14px">HolySpirit</text>
    <text class="arrow-text" x="716" y="236" text-anchor="middle">Descends</text>
  </g>

  <!-- Current earth -->
  <g class="current-stage">
    <text class="stage-label" x="888" y="141" text-anchor="middle">Current</text>
    <text class="stage-label" x="888" y="155" text-anchor="middle">Fallen Earth</text>
    <circle class="outline" cx="890" cy="236" r="61" fill="url(#earth)" role="img" aria-label="Earth seen from space"/>
    <g class="hades">
      <path class="outline" d="M829,366 A61,61 0 0 1 951,366 Z" fill="url(#paradise)" role="img" aria-label="Paradise with clouds and light"/>
      <path class="outline" d="M829,366 A61,61 0 0 0 951,366 Z" fill="url(#torment)" role="img" aria-label="Dark fiery place of torment"/>
      <text class="realm-text" x="889" y="346" text-anchor="middle">Paradise</text>
      <text class="realm-text" x="889" y="400" text-anchor="middle">Torment</text>
    </g>
    <text class="stage-label" x="889" y="452" text-anchor="middle">Hades / Sheol</text>
  </g>

  <!-- After death -->
  <g class="after-death">
    <path class="green-arrow outline" d="M964,183 H1081 V96 H1069 L1104,55 L1139,96 H1128 V229 H964 Z"/>
    <text class="arrow-text" x="1022" y="213" text-anchor="middle">In Jesus</text>
    <text class="arrow-text" transform="translate(1097 108) rotate(90)" style="font-size:15px">Belivers</text>
    <rect class="jesus-red outline" x="1001" y="240" width="130" height="30" rx="15"/>
    <text class="arrow-text" x="1066" y="261" text-anchor="middle">At Death</text>
    <path class="green-arrow outline" d="M1098,280 H1128 V345 A58,58 0 0 1 1070,403 H995 V420 L962,388 L995,356 V373 H1070 A28,28 0 0 0 1098,345 Z"/>
    <text class="arrow-text" x="1040" y="394" text-anchor="middle" style="font-size:12px;letter-spacing:0.5px">Non-believers</text>
  </g>
</svg>
</body>
</html>
```